Brochure Design Project

We need a brochure for our acting school, website is
www.stagelarkhouse.com - It needs to reflect youth, vitality, and people's DREAMS coming true...colors should be red and black, but open to something new as well...the courses included should be
Players' Rapid Forge, Steady Stage Bundle, And The Mastery Track

Emphasis on Players' Rapid Forge is the short term intensity.
Steady Stage Bundle is the benefit of getting all the tools to look for acting work.
Mastery Track is becoming a pro, and if you are in another country, being provided with a visa to come to the U.S.

I have attached pictures and logos...I will submit the copy once there is a framework...the OLD brochure is attached as well...

Thank you...

Marlon

Reason: We would like to see a couple more ideas...

Reason: HI there designers! Thanks for your submissions. We are almost ready to pick a design. Thanks for the understanding.

Target Market(s)

18-35 year olds...fairly affluent, educated, American, European, or Australian

Industry/Entity Type

School

Requirements
Must have
• Make it fun, clean, clear, and NOT corporate.

```html
<!DOCTYPE html>
<html lang="en">
<head>
<meta charset="utf-8">
<title>The Stagelark Troupe – Programs Brochure</title>
<link href="https://fonts.googleapis.com/css2?family=Anton&family=Archivo+Black&family=Open+Sans:wght@400;600;700&display=swap" rel="stylesheet">
<style>
  :root{
    --blue:#1f4e7a;
    --blue-deep:#163a5c;
    --blue-light:#2d6596;
    --magenta:#e5177e;
    --ink:#111317;
    --paper:#f2f3f5;
    --grey:#dde0e4;
    --grey-dark:#c6cbd1;
    --muted:#6b7078;
    --white:#ffffff;
    --stage:#eceef1;
  }
  *{box-sizing:border-box;margin:0;padding:0}
  html,body{width:1200px;height:862px;overflow:hidden;background:var(--stage)}
  body{font-family:"Open Sans",Arial,sans-serif;color:var(--ink);position:relative}

  .spread{position:absolute;left:40px;top:140px;width:780px;height:590px;display:flex;box-shadow:0 6px 20px rgba(0,0,0,.18)}
  .panel{position:relative;width:260px;height:590px;overflow:hidden;background:var(--paper)}
  .panel + .panel{border-left:1px solid var(--grey-dark)}
  .panel-bg{position:absolute;inset:0;width:100%;height:100%}

  .bar{position:absolute;left:14px;right:14px;height:22px;background:var(--ink);color:var(--white);
       font-family:"Archivo Black",Arial,sans-serif;font-size:10.5px;letter-spacing:.3px;
       display:flex;align-items:center;padding-left:9px;text-transform:uppercase}
  .bar .duration{position:absolute;right:0;bottom:-9px;background:var(--magenta);color:var(--white);
       font-size:6.5px;padding:1px 6px;letter-spacing:.5px}
  .copy{position:absolute;left:18px;right:18px;font-size:7.1px;line-height:1.5}
  .copy p + p{margin-top:6px}
  .copy.on-blue{color:var(--white)}
  .copy.on-paper{color:#2b2f35}

  .photo{position:absolute;background:linear-gradient(135deg,#2a2f38 0%,#0f1216 55%,#3b3f46 100%)}
  .photo.warm{background:linear-gradient(135deg,#1b2028 0%,#4a4f58 45%,#0e1014 100%)}

  /* panel 1 */
  .headline{position:absolute;left:14px;top:22px;font-family:"Anton",Impact,sans-serif;font-size:40px;line-height:1;text-transform:uppercase}
  .headline span{display:block;background:var(--white);color:var(--ink);padding:2px 8px 1px;margin-bottom:3px;width:max-content}
  .tag{position:absolute;left:58px;top:160px;background:var(--magenta);color:var(--white);font-family:"Archivo Black",Arial,sans-serif;
       font-size:8px;letter-spacing:1px;padding:2px 10px;text-transform:uppercase}
  .badge{position:absolute;width:38px;height:38px;background:var(--ink);border:2px solid var(--white)}

  /* panel 3 closer */
  .closer{position:absolute;right:0;bottom:40px;width:150px;height:62px;background:var(--ink);color:var(--white);
          font-family:"Archivo Black",Arial,sans-serif;font-size:17px;line-height:1.05;padding:8px 12px}
  .closer em{font-style:normal;color:var(--magenta)}

  /* cover */
  .cover{position:absolute;left:880px;top:140px;width:260px;height:590px;overflow:hidden;background:var(--paper);
         box-shadow:0 6px 20px rgba(0,0,0,.18)}
  .brand{position:absolute;left:0;right:0;top:44px;display:flex;align-items:center;justify-content:center;gap:7px}
  .brand .dot{width:9px;height:9px;border-radius:50%;background:var(--muted)}
  .brand .name{font-family:"Archivo Black",Arial,sans-serif;font-size:14px;color:var(--muted);letter-spacing:.5px;text-transform:uppercase}
  .cover .photo{left:18px;top:112px;width:224px;height:86px}
  .slogan{position:absolute;left:18px;right:18px;top:214px;font-family:"Archivo Black",Arial,sans-serif;
          text-transform:uppercase;line-height:.98;font-size:46px;color:var(--ink)}
  .slogan .line{display:block}
  .program{position:absolute;left:40px;top:468px;font-family:"Archivo Black",Arial,sans-serif;font-size:12px;letter-spacing:.5px;color:var(--white);text-transform:uppercase}
  .motto{position:absolute;left:40px;top:484px;font-family:"Open Sans",Arial,sans-serif;font-weight:600;font-size:12.5px;color:var(--magenta);
         border-right:4px solid var(--magenta);padding-right:6px;background:var(--white);padding-left:4px;margin-left:-4px}
  .web{position:absolute;left:0;right:0;bottom:0;height:40px;line-height:40px;text-align:center;font-size:8px;font-weight:700;
       color:var(--white);letter-spacing:.5px;background:var(--blue-deep)}
</style>
</head>
<body>

<section class="spread" aria-label="Inside spread: programs">

  <article class="panel panel-programs">
    <svg class="panel-bg" viewBox="0 0 260 590" preserveAspectRatio="none" aria-hidden="true">
      <polygon points="0,0 260,0 260,120 0,200" fill="#e4e7eb"/>
      <polygon points="0,60 120,0 260,0 260,40 0,150" fill="#d3d8de"/>
      <polygon points="0,190 260,180 260,350 0,360" fill="#1f4e7a"/>
      <polygon points="160,180 260,180 260,350 210,350" fill="#163a5c"/>
      <polygon points="0,470 260,400 260,590 0,590" fill="#e6e9ed"/>
    </svg>
    <h1 class="headline"><span>What</span><span>We Do</span><span>About It</span></h1>
    <div class="tag">• Programs •</div>

    <div class="bar" style="top:184px">Players' Rapid Forge I<span class="duration">4 Weeks</span></div>
    <div class="copy on-blue" style="top:216px">
      <p>The Players' Rapid Forge I, created by Artistic Director Marlon Ardent, with over 1,200 graduates on CastList, offers an alternative to acting teacher worship: full time, 30 minutes on your feet, daily actors' training. We acknowledge the 21st century by offering only the practical and useful elements of The Harlow Method and The Dorran Approach, as well as the practical application of all this to cold reading and scene study.</p>
      <p>The Players' Rapid Forge I is four weeks of daily classes, by the end of which you will know if acting is your life's work or just a passing fancy.</p>
    </div>

    <div class="badge" style="right:20px;top:355px" aria-hidden="true"></div>
    <div class="bar" style="top:384px;right:60px">Players' Rapid Forge II<span class="duration">8 Weeks</span></div>
    <div class="copy on-paper" style="top:418px">
      <p>The Army's Boot Camp prepares you for war. The Players' Rapid Forge II prepares you for a much tougher battle – Show Business; that's why it's eight glorious weeks of daily work. Because after Rapid Forge II you will never again return to civilian life, you are now an actor. Here you will continue to learn and apply only the relevant aspects of the Harlow Method and the Dorran Approach, you will learn true on-camera skills so that you can work on any type of shoot, and you will learn and APPLY business tools that will get you going in your career.</p>
    </div>
  </article>

  <article class="panel panel-bundle">
    <svg class="panel-bg" viewBox="0 0 260 590" preserveAspectRatio="none" aria-hidden="true">
      <polygon points="0,0 260,0 260,590 0,590" fill="#1f4e7a"/>
      <polygon points="0,0 120,0 0,140" fill="#2d6596"/>
      <polygon points="260,250 260,590 140,590" fill="#163a5c"/>
      <polygon points="0,300 70,290 0,420" fill="#2d6596"/>
    </svg>
    <div class="bar" style="top:26px">The Steady Stage Bundle<span class="duration">3 Months</span></div>
    <div class="copy on-blue" style="top:58px">
      <p>There are those who come to Hollywood, manage to get an audition, go in hoping for the best and fail miserably. There is also something to be said for that kind of pain, yet you only get one shot at a relationship with a casting director, so make it count. The Steady Stage Bundle gives you Rapid Forge I and II plus a personal way to market yourself. It leaves you with one thing: NO EXCUSES. So what are you waiting for?</p>
    </div>
    <div class="photo" style="left:18px;top:170px;width:224px;height:118px" role="img" aria-label="Photo: students filming an on-camera scene in class"></div>

    <div class="bar" style="top:310px">The Advanced Program<span class="duration">Ongoing</span></div>
    <div class="copy on-blue" style="top:342px">
      <p>Only auditioning, committed actors are invited to The Advanced Program. Why? Because we want to invest in getting you in shape and in front of agents, managers and casting directors. During this ongoing course, you will gain a deep understanding of character and script analysis, as well as invaluable experience playing many different kinds of parts in all of the genres you might audition for in today's industry.</p>
    </div>
    <div class="photo warm" style="left:18px;top:448px;width:224px;height:118px" role="img" aria-label="Photo: actors rehearsing a scene on a dark stage"></div>
  </article>

  <article class="panel panel-mastery">
    <svg class="panel-bg" viewBox="0 0 260 590" preserveAspectRatio="none" aria-hidden="true">
      <polygon points="0,0 260,0 260,590 0,590" fill="#1f4e7a"/>
      <polygon points="150,0 260,0 260,200" fill="#163a5c"/>
      <polygon points="0,380 260,440 260,590 0,590" fill="#e6e9ed"/>
      <polygon points="0,380 90,400 0,470" fill="#d3d8de"/>
    </svg>
    <div class="bar" style="top:26px">Mastery Track<span class="duration">2 Years</span></div>
    <div class="copy on-blue" style="top:58px">
      <p>Designed for actors who come to Los Angeles and are committed to turning their dream into reality, the 2 year Mastery Track gets you working on your acting 22 hours a week, every week.</p>
      <p>Utilizing only the effective and updated elements of The Harlow Method and the Dorran Approach, you will learn the craft, the business and on-camera skills in a fully integrated way, and you will be ready to step into the industry as a working actor.</p>
      <p>At the end of the two years you will receive a Stagelark Troupe Mastery Track certificate of completion, something to be proud of in this industry.</p>
      <p>If you are an international student and you can qualify, we will arrange a visa for you to study in the U.S.</p>
    </div>
    <div class="photo" style="left:18px;top:282px;width:224px;height:110px" role="img" aria-label="Photo: actor performing under stage lights"></div>
    <div class="closer">If not <em>now</em>,<br>when?</div>
  </article>
</section>

<section class="cover" aria-label="Front cover">
  <svg class="panel-bg" viewBox="0 0 260 590" preserveAspectRatio="none" aria-hidden="true">
    <polygon points="0,0 260,0 260,590 0,590" fill="#f2f3f5"/>
    <polygon points="0,90 260,0 260,50 0,180" fill="#e1e4e8"/>
    <polygon points="0,420 260,380 260,590 0,590" fill="#1f4e7a"/>
    <polygon points="0,470 150,440 110,590 0,590" fill="#163a5c"/>
    <polygon points="170,590 260,500 260,590" fill="#2d6596"/>
  </svg>
  <div class="brand"><span class="dot" aria-hidden="true"></span><span class="name">The Stagelark Troupe</span></div>
  <div class="photo" role="img" aria-label="Photo: group of students together on stage"></div>
  <h2 class="slogan">
    <span class="line">If not</span>
    <span class="line">now,</span>
    <span class="line">when?</span>
  </h2>
  <div class="program">Players' Rapid Forge</div>
  <div class="motto">Act on your dream</div>
  <div class="web">www.stagelarkhouse.com</div>
</section>

</body>
</html>
```